Calder Vane LED - E- Commerce site

We need a website designed for an LED Billboard company that sells:
1) LED Billboards (Sales & Rental)
2) LED Gas Station lights
3) Truss Systems (Sales & Rental)
4) Sound Systems (Sales & Rental)

Attached are websites that sell similar products as Calder Vane LED. Target market is for business, property managers and event coordinators.
This site will need to be an e-commerce site where customers can purchase the product directly from the site. What I'm looking for is a design layout to start.

Conceptual Web Designs:
http://192.0.2.47:8087/index.html
http://www.pmvdisplay.example/
http://www.auralomaaudio.example/
http://www.quillmarkpanel.example/

Attached is the logo of the company: Please note that the new spelling of the logo is "Calder Vane LED" using domain " CalderVaneLED.com

Industry/Entity Type

Gas Station

Number of Pages Required

5+ page

Requirements
Must have
• 1) E-Commerce - Customers will need to be able to order product from the site.
• 2) Customers will also have the option to rent the product as well.
Nice to have
• I like the image of the attached website, that has a video clip loop
• http://www.quillmarkpanel.example/

```html
<!DOCTYPE html>
<html lang="en">
<head>
<meta charset="utf-8">
<title>Calder Vane LED</title>
<link href="https://fonts.googleapis.com/css2?family=Ubuntu:wght@400;500;700&family=Open+Sans:wght@400;600;700&display=swap" rel="stylesheet">
<style>
:root{
  --red:#e1272b;
  --yellow:#f7c21a;
  --dark:#161616;
  --darker:#111;
  --ink:#222;
  --muted:#777;
  --grey-band:#e8e8e8;
  --line:#dcdcdc;
  --white:#fff;
  --link:#1f6fbf;
}
*{box-sizing:border-box;margin:0;padding:0}
html,body{width:1200px;height:2429px;overflow:hidden}
body{font-family:"Open Sans",Arial,sans-serif;color:var(--ink);background:var(--white);font-size:12px}
.wrap{width:937px;margin-left:131px;position:relative}
h1,h2,h3,h4,.ubuntu{font-family:"Ubuntu",Arial,sans-serif}

/* header */
.site-header{background:var(--dark);height:136px;position:relative}
.top-links{position:absolute;right:132px;top:13px;display:flex;gap:28px;color:#aaa;font-size:11.5px;letter-spacing:.3px;text-transform:uppercase}
.top-links .phone{color:var(--red)}
.brand{position:absolute;left:131px;top:30px;display:flex;align-items:center;gap:10px}
.brand-mark{width:48px;height:48px;border-radius:50%;background:var(--red)}
.brand-name{font-family:"Ubuntu",sans-serif;font-weight:700;font-size:24px;color:var(--yellow);line-height:1.05;width:110px}
.search{position:absolute;left:542px;top:60px;width:332px;height:42px;border:1px solid #3a3a3a;display:flex}
.search span{flex:1;padding:12px 16px;color:#666;font-style:italic;font-size:11px;text-transform:uppercase}
.search i{width:46px;border-left:1px solid #3a3a3a;display:flex;align-items:center;justify-content:center}
.cart{position:absolute;left:900px;top:60px;width:168px;height:42px;border:1px solid #3a3a3a;display:flex;align-items:center;gap:10px;padding-left:16px;color:#eee;font-size:12px;font-weight:600}

/* nav */
.main-nav{background:var(--red);height:47px}
.main-nav ul{list-style:none;display:flex;margin-left:131px;height:47px}
.main-nav li{color:#fff;font-size:13px;text-transform:uppercase;padding:0 19px;line-height:47px;font-weight:500;font-family:"Ubuntu",sans-serif}
.main-nav li.active{background:var(--yellow);color:var(--ink);padding:0 22px}

/* hero */
.hero{height:395px;position:relative;background:linear-gradient(90deg,#5a1d16,#8a3a2a 20%,#3a2218 50%,#7b3a22 80%,#4a1a14)}
.hero-panel{position:absolute;left:131px;top:29px;width:937px;height:334px;overflow:hidden;
  background:radial-gradient(circle at 62% 45%,#4cc0f4,#1a8ed2 45%,#0d63a8 100%)}
.hero-panel h1{position:absolute;left:52px;top:48px;font-size:46px;font-weight:500;color:#fff;letter-spacing:-.5px}
.hero-panel h1 em{font-style:normal;color:var(--yellow)}
.hero-panel ul{position:absolute;left:52px;top:112px;list-style:none;color:#fff;font-size:15px;line-height:28px;text-transform:uppercase}
.hero-actions{position:absolute;left:52px;top:215px;display:flex;gap:10px}
.btn{display:inline-block;font-family:"Ubuntu",sans-serif;font-weight:700;font-size:12px;text-transform:uppercase;text-align:center}
.btn-buy{background:var(--yellow);color:var(--ink)}
.btn-rent{background:var(--red);color:#fff}
.hero-actions .btn{width:103px;height:30px;line-height:30px}
.hero-product{position:absolute;left:395px;top:66px;width:330px;height:230px;border-radius:6px;
  background:radial-gradient(ellipse at 55% 50%,rgba(255,255,255,.55),rgba(220,235,248,.25) 55%,rgba(255,255,255,0) 78%)}
.ribbon{position:absolute;right:-38px;top:22px;width:160px;height:24px;background:var(--red);color:#fff;transform:rotate(45deg);font-size:10px;font-weight:700;text-align:center;line-height:24px;text-transform:uppercase}
.slider-arrows{position:absolute;right:20px;bottom:36px;display:flex;gap:4px}
.slider-arrows span{width:28px;height:28px;background:var(--yellow);display:flex;align-items:center;justify-content:center}

/* categories */
.categories{display:flex;gap:21px;margin-top:31px}
.cat{width:219px;height:158px;position:relative;padding:20px 0 0 22px}
.cat h3{font-size:33px;font-weight:500;line-height:1}
.cat p{font-family:"Ubuntu",sans-serif;color:#fff;font-size:16px;text-transform:uppercase;margin-top:4px}
.cat .btn{position:absolute;left:22px;top:96px;width:103px;height:30px;line-height:30px}
.cat-billboards{background:linear-gradient(135deg,#2f7fc6,#6ab0e6 50%,#4a3a2e)}
.cat-billboards h3{color:var(--yellow)}
.cat-gas{background:linear-gradient(180deg,#0a0f1a,#1b2a44 60%,#c0c6d0)}
.cat-gas h3{color:var(--red)}
.cat-sound{background:linear-gradient(135deg,#1a1a1a,#3a3a3a 60%,#111)}
.cat-sound h3{color:var(--red)}
.cat-truss{background:linear-gradient(135deg,#c21fb0,#e05be0 60%,#8a0f82)}
.cat-truss h3{color:var(--yellow)}

.divider{border:0;border-top:2px solid var(--line);margin-top:33px}

/* featured */
.featured-head{display:flex;justify-content:space-between;align-items:center;margin-top:30px}
.featured-head h2{font-size:19px;font-weight:500;text-transform:uppercase;letter-spacing:.3px}
.filters{display:flex;gap:18px;font-size:11.5px;color:#555;text-transform:uppercase;margin-right:-14px;align-items:center}
.filters .on{background:#ddd;padding:6px 12px;color:#333}
.products{display:grid;grid-template-columns:repeat(4,219px);column-gap:20px;row-gap:34px;margin-top:22px}
.product{border:1px solid var(--line);height:323px;text-align:center}
.product .shot{height:190px;border-bottom:1px solid var(--line);background:radial-gradient(circle,#cfd3d8 0,#eef0f2 42%,#fff 70%)}
.product .shot.dark{background:radial-gradient(circle,#2a2a2a 0,#7a7a7a 35%,#fff 65%)}
.product h4{font-size:13px;font-weight:700;margin-top:18px;line-height:17px}
.product p{font-size:11.5px;color:#666;line-height:18px;margin:7px 10px 0;white-space:nowrap}
.product .actions{display:flex;gap:4px;justify-content:center;margin-top:12px}
.product .btn{width:91px;height:33px;line-height:33px}

/* features */
.features{background:var(--grey-band);height:155px;margin-top:22px}
.features .wrap{display:flex;gap:20px;padding-top:28px}
.feature{width:219px}
.feature h3{font-size:16px;font-weight:500;text-transform:uppercase;letter-spacing:.4px;display:flex;align-items:center;gap:9px;height:22px;line-height:22px}
.feature h3 .ico{width:22px;height:22px;display:flex;align-items:center;justify-content:center;font-size:22px;font-weight:700;line-height:22px}
.feature p{font-size:11.5px;line-height:18px;color:#777;margin-top:10px;width:205px}
.feature a{color:var(--link);font-size:11.5px;text-decoration:none}

/* about */
.about{height:268px}
.about .wrap{display:flex;justify-content:space-between;padding-top:34px}
.about-text{width:448px}
.about h2{font-size:19px;font-weight:500;text-transform:uppercase;letter-spacing:.4px}
.about-text p{font-size:12.5px;line-height:20px;color:#666}
.about-text p:first-of-type{margin-top:26px}
.about-text p+p{margin-top:4px}
.certs{width:445px}
.cert-grid{display:grid;grid-template-columns:repeat(3,1fr);row-gap:28px;column-gap:20px;margin-top:30px}
.cert{height:42px;border-radius:4px}

/* signup */
.signup{background:var(--grey-band);height:87px}
.signup .wrap{display:flex;align-items:center;height:87px}
.signup h4,.connect h4{font-size:14px;font-weight:700;text-transform:uppercase}
.signup-field{margin-left:22px;width:254px;height:33px;background:#fff;color:#999;font-style:italic;font-size:11px;padding:9px 16px}
.signup .btn{width:99px;height:33px;line-height:33px}
.vr{width:1px;height:33px;background:#ccc;margin:0 40px}
.connect{display:flex;align-items:center;gap:22px}
.social{display:flex;gap:9px}
.social span{width:33px;height:33px}

/* footer */
.site-footer{background:var(--darker);height:313px;position:relative}
.footer-cols{display:flex;padding-top:33px}
.footer-col h5{font-family:"Ubuntu",sans-serif;color:var(--yellow);font-size:13px;text-transform:uppercase;font-weight:500;margin-bottom:14px}
.footer-col li{list-style:none;color:#aaa;font-size:11.5px;line-height:24.5px}
.contact-row{display:flex;gap:16px;color:#aaa;font-size:11.5px;line-height:18px;margin-bottom:14px}
.footer-bottom{position:absolute;left:0;right:0;top:256px;border-top:1px solid #2a2a2a}
.footer-bottom .wrap{display:flex;justify-content:space-between;align-items:center;height:57px;color:#999;font-size:11.5px}
.payments{display:flex;align-items:center;gap:12px}
.payments b{font-weight:600;font-size:11px;color:#ddd}
</style>
</head>
<body>

<header class="site-header">
  <div class="brand"><span class="brand-mark"></span><span class="brand-name">Calder Vane LED</span></div>
  <nav class="top-links">
    <span>Customer Service: <span class="phone">+123 555 0190</span></span>
    <span>My Account</span><span>Wish List (0)</span><span>Checkout</span><span>Login</span>
  </nav>
  <div class="search"><span>Search here...</span><i><svg width="14" height="14" viewBox="0 0 14 14"><circle cx="6" cy="6" r="4.5" fill="none" stroke="#e1272b" stroke-width="1.8"/><line x1="9.3" y1="9.3" x2="13" y2="13" stroke="#e1272b" stroke-width="1.8"/></svg></i></div>
  <div class="cart"><svg width="24" height="20" viewBox="0 0 24 20"><path d="M1 2h4l3 11h12l3-8H7" fill="none" stroke="#f7c21a" stroke-width="2"/><circle cx="10" cy="17" r="1.8" fill="#f7c21a"/><circle cx="18" cy="17" r="1.8" fill="#f7c21a"/></svg>0 ITEM(S) - $0.00</div>
</header>

<nav class="main-nav">
  <ul>
    <li class="active">Home</li>
    <li>LED Lights Systems ▾</li>
    <li>Truss Systems</li>
    <li>Sound Systems</li>
    <li>Service and Support</li>
    <li>About</li>
    <li>Contact Us</li>
  </ul>
</nav>

<section class="hero" role="img" aria-label="Blurred city lights and illuminated signs at night">
  <div class="hero-panel">
    <h1><em>LED</em> PANEL LIGHT</h1>
    <ul><li>- Environmental protection</li><li>- Energy saving</li><li>- Green lighting</li></ul>
    <div class="hero-actions"><span class="btn btn-buy">Buy Now!</span><span class="btn btn-rent">On Rent</span></div>
    <div class="hero-product" role="img" aria-label="Two flat LED panel lights"></div>
    <div class="ribbon">New Products</div>
    <div class="slider-arrows">
      <span><svg width="8" height="10"><path d="M6 1L2 5l4 4" fill="none" stroke="#222" stroke-width="2"/></svg></span>
      <span><svg width="8" height="10"><path d="M2 1l4 4-4 4" fill="none" stroke="#222" stroke-width="2"/></svg></span>
    </div>
  </div>
</section>

<main class="wrap">
  <section class="categories">
    <div class="cat cat-billboards" role="img" aria-label="LED billboard against a blue sky"><h3>LED</h3><p>Billboards</p><span class="btn btn-buy">Buy / Rent</span></div>
    <div class="cat cat-gas" role="img" aria-label="Gas station canopy lit at night"><h3>LED GAS</h3><p>Station Lights</p><span class="btn btn-buy">Buy Now</span></div>
    <div class="cat cat-sound" role="img" aria-label="Close-up of loudspeakers"><h3>SOUND</h3><p>Systems</p><span class="btn btn-buy">Buy / Rent</span></div>
    <div class="cat cat-truss" role="img" aria-label="Stage truss lit in magenta"><h3>TRUSS</h3><p>Systems</p><span class="btn btn-buy">Buy / Rent</span></div>
  </section>

  <hr class="divider">

  <div class="featured-head">
    <h2>Featured Products</h2>
    <div class="filters"><span class="on">All</span><span>LED Light</span><span>Gas Station Light</span><span>Truss Systems</span><span>Sound Systems</span></div>
  </div>

  <section class="products">
    <article class="product"><div class="shot" role="img" aria-label="Round recessed LED downlight"></div><h4>30W-LED Panel Light</h4><p>simply dummy text the printing<br>and typesetting industry</p><div class="actions"><span class="btn btn-buy">Buy Now</span><span class="btn btn-rent">On Rent</span></div></article>
    <article class="product"><div class="shot" role="img" aria-label="LED tube light"></div><h4>20W-T8-LED Tube-UL</h4><p>simply dummy text the printing<br>and typesetting industry</p><div class="actions"><span class="btn btn-buy">Buy Now</span><span class="btn btn-rent">On Rent</span></div></article>
    <article class="product"><div class="shot dark" role="img" aria-label="Portable speaker system"></div><h4>Sistema Sonido Portatil USB</h4><p>simply dummy text the printing<br>and typesetting industry</p><div class="actions"><span class="btn btn-buy">Buy Now</span><span class="btn btn-rent">On Rent</span></div></article>
    <article class="product"><div class="shot dark" role="img" aria-label="Stage light mounted on a truss arch"></div><h4>DJ Truss arch</h4><p>simply dummy text the printing<br>and typesetting industry</p><div class="actions"><span class="btn btn-buy">Buy Now</span><span class="btn btn-rent">On Rent</span></div></article>
    <article class="product"><div class="shot dark" role="img" aria-label="Four-deck DJ controller"></div><h4>Mixora DeckQuad</h4><p>simply dummy text the printing<br>and typesetting industry</p><div class="actions"><span class="btn btn-buy">Buy Now</span><span class="btn btn-rent">On Rent</span></div></article>
    <article class="product"><div class="shot" role="img" aria-label="Square LED panel light"></div><h4>30W-LED Panel Light</h4><p>simply dummy text the printing<br>and typesetting industry</p><div class="actions"><span class="btn btn-buy">Buy Now</span><span class="btn btn-rent">On Rent</span></div></article>
    <article class="product"><div class="shot dark" role="img" aria-label="DJ table on a truss stand"></div><h4>DJ Tables &amp; Stands</h4><p>simply dummy text the printing<br>and typesetting industry</p><div class="actions"><span class="btn btn-buy">Buy Now</span><span class="btn btn-rent">On Rent</span></div></article>
    <article class="product"><div class="shot" role="img" aria-label="Pair of T5 LED tubes"></div><h4>Lumaline T5 LED</h4><p>simply dummy text the printing<br>and typesetting industry</p><div class="actions"><span class="btn btn-buy">Buy Now</span><span class="btn btn-rent">On Rent</span></div></article>
  </section>
</main>

<section class="features">
  <div class="wrap">
    <div class="feature"><h3><span class="ico"><svg width="18" height="18" viewBox="0 0 18 18"><circle cx="9" cy="9" r="6" fill="none" stroke="#222" stroke-width="3" stroke-dasharray="3 1.7"/><circle cx="9" cy="9" r="2.2" fill="#222"/></svg></span>Technology</h3><p>t is long established fact the reader will be distracted by the readable content of a page...</p><a>Read More »</a></div>
    <div class="feature"><h3><span class="ico">%</span>Price</h3><p>t is long established fact the reader will be distracted by the readable content of a page...</p><a>Read More »</a></div>
    <div class="feature"><h3><span class="ico"><svg width="20" height="18" viewBox="0 0 20 18"><rect x="1" y="3" width="14" height="14" fill="none" stroke="#222" stroke-width="2"/><path d="M4 9l4 4 10-12" fill="none" stroke="#222" stroke-width="2.5"/></svg></span>Quality</h3><p>t is long established fact the reader will be distracted by the readable content of a page...</p><a>Read More »</a></div>
    <div class="feature"><h3><span class="ico"><svg width="18" height="18" viewBox="0 0 18 18"><circle cx="9" cy="9" r="8" fill="none" stroke="#222" stroke-width="2"/><path d="M9 4l1.5 3.2 3.5.4-2.6 2.4.7 3.5L9 11.8l-3.1 1.7.7-3.5L4 7.6l3.5-.4z" fill="#222"/></svg></span>Warranty</h3><p>t is long established fact the reader will be distracted by the readable content of a page...</p><a>Returns Policy »</a></div>
  </div>
</section>

<section class="about">
  <div class="wrap">
    <div class="about-text">
      <h2>About Calder Vane LED</h2>
      <p>It is a long established fact that a reader will be distracted by the readable content of a page when looking at its layout. The point of using Lorem Ipsum is that it has a more-or-less normal distribution of Content here, content here, making it look like readable English.</p>
      <p>Many desktop publishing packages and web page editors now use Lorem Ipsum as their default model text, and a search for 'lorem ipsum' will uncover many web sites still in their infancy...</p>
    </div>
    <div class="certs">
      <h2>Product Certification</h2>
      <div class="cert-grid" aria-label="Certification badges">
        <span class="cert" style="background:#c9c9c9"></span>
        <span class="cert" style="background:#2b2b2b"></span>
        <span class="cert" style="background:#8f1d22"></span>
        <span class="cert" style="background:#d8232a"></span>
        <span class="cert" style="background:#2a8fd0"></span>
        <span class="cert" style="background:#2f8a3a"></span>
      </div>
    </div>
  </div>
</section>

<section class="signup">
  <div class="wrap">
    <h4>Sign up for deals:</h4>
    <div class="signup-field">Enter Your Email</div>
    <span class="btn btn-buy">Sign Up</span>
    <span class="vr"></span>
    <div class="connect"><h4>Stay Connected:</h4>
      <div class="social">
        <span style="background:#3b5998" aria-label="Social profile 1"></span>
        <span style="background:#29a9e1" aria-label="Social profile 2"></span>
        <span style="background:#0e76a8" aria-label="Social profile 3"></span>
        <span style="background:#dd4b39" aria-label="Social profile 4"></span>
      </div>
    </div>
  </div>
</section>

<footer class="site-footer">
  <div class="wrap footer-cols">
    <div class="footer-col" style="width:160px"><h5>Quick Links</h5><ul><li>Home</li><li>Products</li><li>Services</li><li>About Us</li><li>FAQ's</li></ul></div>
    <div class="footer-col" style="width:172px"><h5>Need Help?</h5><ul><li>See All Help</li><li>Returns</li><li>Shipping</li><li>Warranty</li><li>Contact Us</li></ul></div>
    <div class="footer-col" style="width:214px"><h5>Policies &amp; Info</h5><ul><li>Terms and Conditions</li><li>Policy for Sellers</li><li>Policy for Buyers</li><li>Shipping &amp; Refund Policies</li><li>Wholesale Policy</li><li>Privacy Policy</li></ul></div>
    <div class="footer-col" style="width:188px"><h5>My Account</h5><ul><li>Sign in</li><li>Track Order</li></ul></div>
    <div class="footer-col"><h5>Contact Us</h5>
      <div class="contact-row"><svg width="12" height="16" viewBox="0 0 12 16"><path d="M6 0a6 6 0 0 0-6 6c0 4.5 6 10 6 10s6-5.5 6-10a6 6 0 0 0-6-6z" fill="#888"/><circle cx="6" cy="6" r="2.2" fill="#111"/></svg><span>Lorem Ipsum is simply dummy<br>Halden, AB T0X 4R2</span></div>
      <div class="contact-row"><svg width="12" height="14" viewBox="0 0 12 14"><path d="M2 0l3 3-1.5 2a9 9 0 0 0 4 4L9 7.5l3 3-2 2.5C5 12 0 7 .5 2z" fill="#888"/></svg><span>Phone:<br>(123) 555 0190</span></div>
      <div class="contact-row"><svg width="12" height="10" viewBox="0 0 12 10"><rect width="12" height="10" fill="#888"/><path d="M0 0l6 5 6-5" fill="none" stroke="#111" stroke-width="1.2"/></svg><span>Email:<br>info@caldervaneled.com</span></div>
    </div>
  </div>
  <div class="footer-bottom">
    <div class="wrap">
      <span>Copyright © 2016 - Calder Vane LED, All Rights Reserved</span>
      <div class="payments"><span>Accepted Payment :</span><b>Mondo</b><b>PayRiver</b><b>Vantix</b><b>Marcard</b></div>
    </div>
  </div>
</footer>

</body>
</html>
```